Brindlewick Solutions Ltd

I'd like to create a company letterhead for the attached logo in word format.

I'd like to emphasis the icon in large translucent state from the left corner and ensure that the letterhead colouring matches the colour palette of the current logo with a contrast so it's clear to see. I've attached a copy of our sister company page on the app for reference.

```html
<!DOCTYPE html>
<html lang="en">
<head>
<meta charset="utf-8">
<title>Brindlewick Solutions Ltd — Letterhead</title>
<link rel="stylesheet" href="https://fonts.googleapis.com/css2?family=Lato:wght@400;700&family=Open+Sans:wght@400&display=swap">
<style>
  :root {
    --teal: #13b8a6;
    --grey: #9b9b9b;
    --ink: #1c1c1c;
    --paper: #ffffff;
    --backdrop: #f2f2f2;
    --signature-tone: #e9e9e9;
  }
  html, body {
    margin: 0;
    width: 1040px;
    height: 1200px;
    overflow: hidden;
    background: var(--backdrop);
  }
  .letterhead {
    position: absolute;
    left: 96px;
    top: 0;
    width: 848px;
    height: 1200px;
    background: var(--paper);
    font-family: "Lato", sans-serif;
    color: var(--ink);
    overflow: hidden;
  }
  .brand {
    position: absolute;
    left: 42px;
    top: 150px;
    display: flex;
    align-items: center;
    gap: 12px;
    font-weight: 400;
    font-size: 30px;
    line-height: 1.1;
    color: var(--teal);
  }
  .brand-dot {
    width: 26px;
    height: 26px;
    border-radius: 50%;
    background: var(--teal);
    flex: none;
  }
  .contact {
    position: absolute;
    left: 585px;
    top: 76px;
    padding-left: 18px;
    border-left: 2px solid var(--teal);
    font-family: "Open Sans", sans-serif;
    font-size: 15px;
    line-height: 18.6px;
  }
  .contact p { margin: 0; }
  .contact .address { margin-bottom: 10px; }
  .contact-line { display: flex; align-items: center; gap: 4px; }
  .contact-line svg { width: 10px; height: 10px; fill: var(--teal); flex: none; }

  .letter {
    position: absolute;
    left: 42px;
    top: 275px;
    width: 764px;
    font-size: 17px;
  }
  .letter p { margin: 0; }
  .date, .recipient, .company-address { line-height: 20px; }
  .date { margin-bottom: 22px !important; }
  .recipient { margin-bottom: 19px !important; }
  .company-address { margin-bottom: 23px !important; }
  .salutation {
    font-size: 22px;
    font-weight: 700;
    line-height: 26px;
    margin-bottom: 20px !important;
  }
  .body-copy {
    text-align: justify;
    line-height: 18.6px;
    margin-bottom: 18.4px !important;
  }
  .closing { margin-top: 42px !important; line-height: 20px; }

  .signature {
    position: absolute;
    left: 42px;
    top: 966px;
    width: 180px;
    height: 42px;
    background: var(--signature-tone);
  }
  .footer-rule {
    position: absolute;
    left: 0;
    bottom: 86px;
    width: 848px;
    height: 4px;
    background: var(--grey);
  }
  .footer-band {
    position: absolute;
    left: 0;
    bottom: 0;
    width: 848px;
    height: 76px;
    background: var(--teal);
  }
</style>
</head>
<body>
  <main class="letterhead">
    <header>
      <div class="brand"><span class="brand-dot"></span><span>Brindlewick Solutions Ltd</span></div>
      <div class="contact">
        <p class="address">418 Alderbrook Ln, Suite 12<br>Harlow Bay, OR 97031</p>
        <p class="contact-line"><svg viewBox="0 0 10 10"><path d="M2 1l2 2-1 1c.6 1.3 1.7 2.4 3 3l1-1 2 2-1.5 1.5C4 9 1 6 .5 2.5z"/></svg>(555) 014-3826</p>
        <p class="contact-line"><svg viewBox="0 0 10 10"><path d="M0 2h10v6H0z"/></svg>info@website.com</p>
        <p class="contact-line"><svg viewBox="0 0 10 10"><circle cx="5" cy="5" r="5"/></svg>www.website.com</p>
      </div>
    </header>

    <section class="letter">
      <p class="date">January-03-2020</p>
      <p class="recipient">Mr, John Doe<br>President</p>
      <p class="company-address">Marrowgate Holdings<br>123 Street Name, Suite# 10<br>City, State, 120023</p>
      <p class="salutation">Dear Mr, John</p>
      <p class="body-copy">Lorem ipsum dolor sit amet, consectetur adipiscing elit, sed do eiusmod tempor incididunt ut labore et dolore magna aliqua. Ut enim ad minim veniam, quis nostrud exercitation ullamco laboris nisi ut aliquip ex ea commodo consequat. Duis aute irure dolor in reprehenderit in voluptate velit esse cillum dolore eu fugiat nulla pariatur.</p>
      <p class="body-copy">Lorem ipsum dolor sit amet, consectetur adipiscing elit, sed do eiusmod tempor incididunt ut labore et dolore magna aliqua. Ut enim ad minim veniam, quis nostrud exercitation ullamco laboris nisi ut aliquip ex ea commodo consequat. Duis aute irure dolor in reprehenderit in voluptate velit esse cillum dolore eu fugiat nulla pariatur.</p>
      <p class="body-copy">Lorem ipsum dolor sit amet, consectetur adipiscing elit, sed do eiusmod tempor incididunt ut labore et dolore magna aliqua. Ut enim ad minim veniam, quis nostrud exercitation ullamco laboris nisi ut aliquip ex ea commodo consequat.</p>
      <p class="body-copy">Excepteur sint occaecat cupidatat non proident, sunt in culpa qui officia deserunt mollit anim id est laborum. re et dolore magnam aliquam quaerat voluptatem.</p>
      <p class="closing">Regards</p>
    </section>

    <div class="signature" role="img" aria-label="Handwritten signature of the sender"></div>

    <footer>
      <div class="footer-rule"></div>
      <div class="footer-band"></div>
    </footer>
  </main>
</body>
</html>
```